Veltrano.co - Polar Expeditions Specialists

We need a modern, visually striking business card for Veltrano.co, a company specialized in selling expedition cruises to the most remote regions on Earth, with a focus on the Arctic and Antarctica. The design should instantly communicate that the cardholder is an expert in polar travel. Use clean, premium aesthetics with cool tones like icy blue and white, possibly incorporating polar imagery (ice, glaciers, penguins, etc.)

Attached the logo

Contact Information for Business Card

Feels high-end and trustworthy.. Visually memorable — encourages people to keep it

Colors
0054AA
0677BA
7BADD7
CADEEF
E8F1F8

Requirements
Must have
• ice, glaciers, penguins, montains
Nice to have
• modern, transparente,

```html
<!DOCTYPE html>
<html lang="en">
<head>
<meta charset="UTF-8">
<title>Veltrano.co – Business Card</title>
<link rel="stylesheet" href="https://fonts.googleapis.com/css2?family=Poppins:wght@600;700&family=Roboto:wght@400&display=swap">
<style>
  :root {
    --page-bg: #1a1c21;
    --card-navy: #0b1629;
    --card-navy-deep: #0a1745;
    --brand-blue: #2f7fd0;
    --band-blue-a: #2b4fc4;
    --band-blue-b: #2f7fd0;
    --art-blue-a: #2a5bc9;
    --art-blue-b: #2b7fcf;
    --edge-blue: #2c5fd0;
    --text-white: #f2f6fb;
  }
  * { margin: 0; padding: 0; box-sizing: border-box; }
  html, body { width: 1200px; height: 840px; overflow: hidden; }
  body {
    background: var(--page-bg);
    position: relative;
    font-family: "Roboto", Arial, sans-serif;
  }
  .card {
    position: absolute;
    width: 560px;
    height: 320px;
    border-radius: 22px;
    overflow: hidden;
    background: linear-gradient(125deg, var(--card-navy) 45%, var(--card-navy-deep) 75%, var(--card-navy) 100%);
    box-shadow: 0 0 0 2px var(--edge-blue), 0 18px 40px rgba(0,0,0,.5);
  }
  .card--back { left: 60px; top: 80px; }
  .card--front { left: 580px; top: 440px; }

  .wordmark {
    font-family: "Poppins", Arial, sans-serif;
    font-weight: 700;
    color: var(--brand-blue);
    line-height: 1;
    letter-spacing: .5px;
  }
  .tagline {
    font-family: "Poppins", Arial, sans-serif;
    font-weight: 600;
    color: var(--brand-blue);
  }

  /* back */
  .back-brand {
    position: absolute;
    left: 0; right: 0; top: 118px;
    text-align: center;
  }
  .back-brand .wordmark { font-size: 58px; }
  .back-brand .tagline { font-size: 15px; margin-top: 6px; }

  /* front */
  .front-art {
    position: absolute;
    left: 44px; top: 64px;
    width: 290px; height: 190px;
    border-radius: 120px 120px 0 0;
    background: linear-gradient(160deg, var(--art-blue-b) 0%, var(--art-blue-a) 55%, var(--art-blue-b) 100%);
  }
  .front-band {
    position: absolute;
    left: 0; right: 0; bottom: 0;
    height: 70px;
    background: linear-gradient(90deg, var(--band-blue-a) 0%, var(--band-blue-a) 40%, var(--band-blue-b) 100%);
  }
  .address {
    position: absolute;
    right: 40px; bottom: 24px;
    color: var(--text-white);
    font-size: 15px;
  }
  .front-info {
    position: absolute;
    right: 32px; top: 26px;
    text-align: right;
  }
  .front-info .wordmark { font-size: 42px; }
  .front-info .tagline { font-size: 12px; margin-top: 4px; }
  .person-name {
    margin-top: 14px;
    font-size: 16px;
    color: var(--brand-blue);
    letter-spacing: .5px;
  }
  .person-role { font-size: 14px; color: var(--text-white); margin-top: 2px; }
  .contact-list { list-style: none; margin-top: 16px; }
  .contact-list li {
    display: flex; justify-content: flex-end; align-items: center; gap: 6px;
    font-size: 13px; color: var(--text-white); line-height: 19px;
  }
  .contact-list svg { width: 12px; height: 12px; stroke: var(--brand-blue); fill: none; stroke-width: 1.4; }
</style>
</head>
<body>

<section class="card card--back">
  <div class="back-brand">
    <div class="wordmark">Veltrano.co</div>
    <div class="tagline">Polar Expeditions Specialists</div>
  </div>
</section>

<section class="card card--front">
  <div class="front-art" role="img" aria-label="Blue silhouette illustration of a polar bear looking up at stars with two penguins standing on the ice"></div>
  <div class="front-band">
    <p class="address">Your address, city, state, ZIP 0000</p>
  </div>
  <div class="front-info">
    <div class="wordmark">Veltrano.co</div>
    <div class="tagline">Polar Expeditions Specialists</div>
    <p class="person-name">MARCUS LINDQVIST</p>
    <p class="person-role">Manager</p>
    <ul class="contact-list">
      <li>555-310-4820
        <svg viewBox="0 0 12 12"><path d="M3 1l2 2.5-1.2 1.2a6 6 0 0 0 3.5 3.5L8.5 7 11 9l-1.2 1.6C6 11 1 6 1.4 2.2z"/></svg>
      </li>
      <li>hello@veltrano.co
        <svg viewBox="0 0 12 12"><rect x="1" y="2.5" width="10" height="7"/><path d="M1 2.5l5 4 5-4"/></svg>
      </li>
      <li>www.veltrano.co
        <svg viewBox="0 0 12 12"><circle cx="6" cy="6" r="5"/><ellipse cx="6" cy="6" rx="2.2" ry="5"/><path d="M1 6h10"/></svg>
      </li>
    </ul>
  </div>
</section>

</body>
</html>
```